Onboarding Infographic/brochure

We are a small criminal defense firm looking to create some sort of infographic or brochure that we can onboard new clients with. We are currently sending it out via email but want something a bit cooler and fun to send to clients. The information is:

A Few Quick Rules

We are here to help each step of the way. While questions are never discouraged, this letter will answer some of the most common ones we get asked.

Communications

As a client, you should always be in the loop. While we will try to respond to questions as quickly as possible, sometimes we are unable to respond right away. Do not worry - we promise to get back to you soon. Some questions might take some time to research, and a correct answer is better than a quick one.

Appointments

One of the benefits of having an attorney is the ability to discuss your case outside of court, minus the stress and headaches. If you need an appointment, please contact the office.

Appointments must be scheduled in advance. We do not want you to make a special trip to the office only to learn that we are in court or otherwise unavailable.

Jail Visits

If your family member is currently in jail, we take that very seriously. We will visit your loved one and introduce ourselves. While the case is ongoing, we ask that a family member be designated a “contact” person so that messages can be relayed quickly. Never discuss the facts of the case over the phone with someone who is in jail. Jail calls are recorded and we have seen too many cases go south based on remarks made over recorded lines.

Police Reports and Discovery

We will do our best to provide you with copies of everything we receive on your case. Most information will be emailed, so please keep your email address up to date.

Changes in Contact Information

If you move or change numbers during the case, please let us know. It is difficult to help if we are unable to reach you, and helping you is why we are here.

Court Appearances

Cases do not get resolved as quickly as they do on television. Expect there to be several hearings in your case and it may be necessary for you to attend one or more of them. If a hearing is set, you will receive notice of the date and time of each hearing.

Billing and Collections

We understand that this investment was a huge decision for you. As we focus on providing the best representation, we will need for you to stay on schedule with any payment arrangements agreed to at the time of your initial consultation.

Again, thank you for your trust in us. We look forward to getting a fantastic outcome on your case.

Target Market(s)

Criminal defense clients and their families

Industry/Entity Type

Legal

Font styles to use
Serif

Requirements
Must have
• Must incorporate all of the rules we email out. Would like diagrams, images or pictures
Nice to have
• We attached a Welcome brochure. Not sure I want it to look super similar, hence the request for infographic.

```html
<!DOCTYPE html>
<html lang="en">
<head>
<meta charset="utf-8">
<title>Northgate Legal Group – A Few Quick Rules</title>
<link href="https://fonts.googleapis.com/css2?family=Montserrat:wght@500;600;700&family=Raleway:ital,wght@0,400;0,500;1,400&display=swap" rel="stylesheet">
<style>
  :root {
    --bg-top: #1f2b3d;
    --bg-bottom: #162131;
    --panel-a: #1f3d63;
    --panel-b: #142540;
    --frame: #c7d0dc;
    --ink: #ffffff;
    --ink-soft: #e4e9f0;
    --accent: #3a8ad4;
    --accent-soft: #7db2ec;
    --orange: #f26b22;
  }
  * { box-sizing: border-box; margin: 0; padding: 0; }
  html, body { width: 1200px; height: 3519px; overflow: hidden; }
  body {
    background: linear-gradient(180deg, var(--bg-top) 0%, var(--bg-bottom) 100%);
    font-family: "Raleway", Arial, sans-serif;
    color: var(--ink);
    position: relative;
  }
  .brand {
    position: absolute; top: 190px; left: 0; width: 1200px;
    text-align: center; font-family: "Montserrat", Arial, sans-serif;
    font-weight: 700; font-size: 64px; letter-spacing: 2px; color: var(--ink);
    line-height: 1.4;
  }
  .brand small {
    display: block; font-size: 34px; letter-spacing: 16px; font-weight: 700; line-height: 1.2;
  }
  .divider {
    position: absolute; top: 361px; left: 255px; width: 690px; height: 3px;
    background: linear-gradient(90deg, transparent, #dfe5ee 50%, transparent);
  }
  .title {
    position: absolute; top: 410px; width: 1200px; text-align: center;
    font-family: "Montserrat", Arial, sans-serif; font-weight: 700;
    font-size: 68px; color: var(--accent); letter-spacing: -1px;
  }
  .intro {
    position: absolute; top: 502px; width: 1200px; text-align: center;
    font-size: 26px; line-height: 34px; color: var(--ink-soft);
  }
  .rules { position: absolute; top: 642px; left: 68px; width: 1064px; }
  .rule {
    display: flex; height: 340px; margin-bottom: 29px;
    border: 2px solid var(--frame); position: relative;
  }
  .rule.flip { flex-direction: row-reverse; }
  .rule-photo { width: 465px; flex: none; }
  .rule-body {
    flex: 1; display: flex; flex-direction: column; justify-content: center;
    padding: 0 24px 0 86px;
    background: linear-gradient(135deg, var(--panel-a) 0%, var(--panel-b) 100%);
  }
  .rule.flip .rule-body { padding: 0 80px 0 45px; }
  .rule h2 {
    font-family: "Montserrat", Arial, sans-serif; font-weight: 700;
    font-size: 42px; line-height: 52px; margin-bottom: 18px; letter-spacing: -0.3px;
  }
  .rule p { font-size: 19.5px; line-height: 24px; color: var(--ink-soft); }
  .rule p + p { margin-top: 24px; }
  .hl { font-style: italic; color: var(--accent-soft); }
  .notch { position: absolute; top: 140px; width: 30px; height: 60px; }
  .rule .notch { left: 463px; }
  .rule.flip .notch { left: auto; right: 463px; transform: scaleX(-1); }
  .photo-support { background: linear-gradient(135deg, #cfd6de, #e9e4df 55%, #b9c3cc); }
  .photo-meeting { background: linear-gradient(135deg, #4a4540, #a89a86 55%, #3a3532); }
  .photo-jail { background: linear-gradient(135deg, #5f6668, #a9b1b3 50%, #7d8587); }
  .photo-files { background: linear-gradient(135deg, #5f84b3, #bcd0e6 50%, #36506f); }
  .photo-phone { background: linear-gradient(135deg, #6e4a2a, #e9e6e2 50%, #8a6035); }
  .photo-court { background: linear-gradient(135deg, #8a5a32, #c4955f 50%, #6b4326); }
  .photo-bills { background: linear-gradient(135deg, #27b6d6, #e9dfcf 55%, #2cc0de); }
  .closing {
    position: absolute; top: 3272px; width: 1200px; text-align: center;
    font-size: 27px; line-height: 34px; color: var(--ink-soft);
  }
  .web {
    position: absolute; top: 3438px; left: 332px; width: 538px; height: 81px;
    background: var(--orange); border-radius: 22px 22px 0 0;
    display: flex; align-items: center; justify-content: center;
    font-family: "Montserrat", Arial, sans-serif; font-weight: 600;
    font-size: 25px; letter-spacing: 2px; color: var(--ink);
  }
</style>
</head>
<body>
  <div class="brand">NORTHGATE<small>LEGAL GROUP</small></div>
  <div class="divider"></div>
  <h1 class="title">A Few Quick Rules</h1>
  <p class="intro">We are here to help each step of the way. While questions are never discouraged,<br>this letter will answer some of the most common ones we get asked.</p>

  <main class="rules">
    <section class="rule">
      <div class="rule-photo photo-support" role="img" aria-label="Photo of a smiling support agent wearing a headset beside a colleague on the phone"></div>
      <svg class="notch" viewBox="0 0 30 60"><path d="M0 0 L30 30 L0 60" fill="none" stroke="#c7d0dc" stroke-width="2"/></svg>
      <div class="rule-body">
        <h2>Communications</h2>
        <p>As a client, you should always be in the loop. While we will try to respond to questions as quickly as possible, sometimes we are unable to respond right away. Do not worry - we promise to get back to you soon. <span class="hl">Some questions might take some time to research, and a correct answer is better than a quick one.</span></p>
      </div>
    </section>

    <section class="rule flip">
      <div class="rule-photo photo-meeting" role="img" aria-label="Photo of an attorney meeting clients across a desk with a laptop"></div>
      <svg class="notch" viewBox="0 0 30 60"><path d="M0 0 L30 30 L0 60" fill="none" stroke="#c7d0dc" stroke-width="2"/></svg>
      <div class="rule-body">
        <h2>Appointments</h2>
        <p>One of the benefits of having an attorney is the ability to discuss your case outside of court, minus the stress and headaches. If you need an appointment, please contact the office.</p>
        <p><span class="hl">Appointments must be scheduled in advance.</span> We do not want you to make a special trip to the office only to learn that we are in court or otherwise unavailable.</p>
      </div>
    </section>

    <section class="rule">
      <div class="rule-photo photo-jail" role="img" aria-label="Photo of a man in an orange jumpsuit seated at a grey visiting table"></div>
      <svg class="notch" viewBox="0 0 30 60"><path d="M0 0 L30 30 L0 60" fill="none" stroke="#c7d0dc" stroke-width="2"/></svg>
      <div class="rule-body">
        <h2>Jail Visits</h2>
        <p><span class="hl">If your family member is currently in jail, we take that very seriously.</span> We will visit your loved one and introduce ourselves. While the case is ongoing, we ask that a family member be designated a “contact” person so that messages can be relayed quickly. <span class="hl">Never discuss the facts of the case over the phone with someone who is in jail.</span> Jail calls are recorded and we have seen too many cases go south based on remarks made over recorded lines.</p>
      </div>
    </section>

    <section class="rule flip">
      <div class="rule-photo photo-files" role="img" aria-label="Photo of hands leafing through a binder of documents"></div>
      <svg class="notch" viewBox="0 0 30 60"><path d="M0 0 L30 30 L0 60" fill="none" stroke="#c7d0dc" stroke-width="2"/></svg>
      <div class="rule-body">
        <h2>Police Reports and Discovery</h2>
        <p>We will do our best to provide you with copies of everything we receive on your case. <span class="hl">Most information will be emailed,</span> so please keep your email address up to date.</p>
      </div>
    </section>

    <section class="rule">
      <div class="rule-photo photo-phone" role="img" aria-label="Photo of a smartphone showing a dial pad on a wooden table"></div>
      <svg class="notch" viewBox="0 0 30 60"><path d="M0 0 L30 30 L0 60" fill="none" stroke="#c7d0dc" stroke-width="2"/></svg>
      <div class="rule-body">
        <h2>Changes in Contact Information</h2>
        <p><span class="hl">If you move or change numbers during the case, please let us know.</span> It is difficult to help if we are unable to reach you, and helping you is why we are here.</p>
      </div>
    </section>

    <section class="rule flip">
      <div class="rule-photo photo-court" role="img" aria-label="Photo of an empty wood-panelled courtroom with flags behind the bench"></div>
      <svg class="notch" viewBox="0 0 30 60"><path d="M0 0 L30 30 L0 60" fill="none" stroke="#c7d0dc" stroke-width="2"/></svg>
      <div class="rule-body">
        <h2>Court Appearances</h2>
        <p>Cases do not get resolved as quickly as they do on television. <span class="hl">Expect there to be several hearings in your case and it may be necessary for you to attend one or more of them.</span> If a hearing is set, you will receive notice of the date and time of each hearing.</p>
      </div>
    </section>

    <section class="rule">
      <div class="rule-photo photo-bills" role="img" aria-label="Illustration of a bill in an envelope examined with a magnifying glass"></div>
      <svg class="notch" viewBox="0 0 30 60"><path d="M0 0 L30 30 L0 60" fill="none" stroke="#c7d0dc" stroke-width="2"/></svg>
      <div class="rule-body">
        <h2>Billing and Collections</h2>
        <p>We understand that this investment was a huge decision for you. <span class="hl">As we focus on providing the best representation, we will need for you to stay on schedule with any payment arrangements agreed to</span> at the time of your initial consultation.</p>
      </div>
    </section>
  </main>

  <p class="closing">Again, <span style="color: var(--accent-soft)">thank you for your trust in us.</span> We look forward to<br>getting a fantastic outcome on your case.</p>
  <div class="web">www.northgatelegalgroup.com</div>
</body>
</html>
```